Plumbing Product Supply Company Needs Front & Back Cover Design For Instruction Manuals

We need a front and back over design for our instruction manuals that we need to give to clients.

There will also be a picture of the product on the front cover so please use the supplied image as dummy.

it needs to incorporate our logo and branding colours.

We are the industry leader so it needs to be up-market, professional and stand out from the crowd.

Target Market(s)

Plumbing Companies

Industry/Entity Type

Plumbing

Font styles to use
Sans Serif

Colors
abd036
ffffff
000000
eaeaea
cbcbcb

Requirements
Must have
• Front & Back Cover as it will become a booklet.
• The logo is to be on the black background.
Nice to have
• Professional, modern, sleek.
Should not have
• Other colours that what is on the guidelines.

```html
<!DOCTYPE html>
<html lang="en">
<head>
<meta charset="utf-8">
<title>Southland Relining Supplies – Manual Covers</title>
<link rel="stylesheet" href="https://fonts.googleapis.com/css2?family=Jost:wght@400;500&family=Lato:wght@400&display=swap">
<style>
  :root {
    --brand-green: #abd036;
    --brand-green-deep: #5a9a2a;
    --black: #000000;
    --cover-black: #050608;
    --white: #ffffff;
    --light-grey: #eaeaea;
    --mid-grey: #cbcbcb;
    --paper: #f4f5f7;
  }
  * { margin: 0; padding: 0; box-sizing: border-box; }
  html, body {
    width: 1200px;
    height: 897px;
    overflow: hidden;
    background: var(--light-grey);
  }
  .canvas {
    position: relative;
    width: 1200px;
    height: 897px;
  }
  .cover {
    position: absolute;
    top: 106px;
    width: 484px;
    height: 684px;
    overflow: hidden;
  }
  .cover--back { left: 102px; background: var(--cover-black); }
  .cover--front { left: 614px; background: var(--paper); }

  .brand-name {
    position: absolute;
    left: 0;
    width: 100%;
    text-align: center;
    font-family: "Jost", sans-serif;
    font-weight: 500;
    color: var(--brand-green);
    text-transform: uppercase;
    letter-spacing: 3px;
    line-height: 1.15;
  }
  .brand-name__lead { display: block; font-size: 46px; letter-spacing: 4px; }
  .brand-name__rest { display: block; font-size: 22px; margin-top: 6px; }
  .cover--back .brand-name { top: 284px; }
  .cover--front .brand-name { top: 62px; z-index: 2; }

  .contact {
    position: absolute;
    left: 0;
    bottom: 46px;
    width: 100%;
    text-align: center;
    color: var(--white);
    font-family: "Lato", sans-serif;
  }
  .contact__title { font-size: 15px; margin-bottom: 4px; }
  .contact__line { font-size: 9px; line-height: 1.3; }

  .front-art {
    position: absolute;
    inset: 0;
  }
  .product-photo {
    position: absolute;
    left: 34px;
    top: 326px;
    width: 408px;
    height: 316px;
    border-radius: 4px;
    background: radial-gradient(ellipse at 50% 45%, #8a8f94 0%, #c9ccd0 45%, var(--paper) 80%);
  }
  .footer-band {
    position: absolute;
    left: 0;
    bottom: 0;
    width: 100%;
    height: 16px;
    background: var(--mid-grey);
  }
</style>
</head>
<body>
<main class="canvas">

  <section class="cover cover--back" aria-label="Back cover">
    <h2 class="brand-name">
      <span class="brand-name__lead">Southland</span>
      <span class="brand-name__rest">Relining Supplies</span>
    </h2>
    <div class="contact">
      <p class="contact__title">Contact Us:</p>
      <p class="contact__line">Lorem ipsum Lorem ipsum Lorem ipsum Lorem ipsum</p>
      <p class="contact__line">Email: youremail@gmail.com | Ph: 000 000 0000 | Fax: 000 000 0000</p>
    </div>
  </section>

  <section class="cover cover--front" aria-label="Front cover">
    <svg class="front-art" width="484" height="684" viewBox="0 0 484 684" aria-hidden="true">
      <path d="M0 0 H484 V262 C420 300 340 288 260 260 C190 236 110 226 0 290 Z" fill="var(--cover-black)"/>
      <path d="M0 300 C90 250 170 236 250 256 C330 278 400 312 484 276 V282 C400 318 330 288 250 266 C170 246 100 258 0 306 Z" fill="var(--brand-green)"/>
      <path d="M0 320 C100 262 175 250 255 272 C335 295 405 336 484 300 V318 C400 350 330 312 250 290 C170 268 100 276 0 334 Z" fill="var(--brand-green-deep)"/>
    </svg>
    <h1 class="brand-name">
      <span class="brand-name__lead">Southland</span>
      <span class="brand-name__rest">Relining Supplies</span>
    </h1>
    <div class="product-photo" role="img" aria-label="Product photo: pipe relining kit with tool case, chemical containers, hoses, liner rolls and rods"></div>
    <div class="footer-band"></div>
  </section>

</main>
</body>
</html>
```